Business Cards for a law firm

Business cards for our law firm. Use our silhoette logo and OAK PARTNERS - check our website (www.oakpartners.example)

Contact Information for Business Card

our silhouette logo, OAK PARTNERS, 800-555-0147, Dorian Pemberton, dorian@oakpartners.example

Requirements
Must have
• our silhouette logo, OAK PARTNERS, 800-555-0147, Dorian Pemberton, dorian@oakpartners.example

```html
<!DOCTYPE html>
<html lang="en">
<head>
<meta charset="utf-8">
<title>Oak Partners Business Cards</title>
<link rel="stylesheet" href="https://fonts.googleapis.com/css2?family=Marcellus+SC&family=Montserrat:wght@600&display=swap">
<style>
  :root {
    --backdrop: #6f6f70;
    --card-dark: #202d63;
    --card-light: #283a7a;
    --ink: #ffffff;
    --ink-soft: #dfe4f3;
  }
  * { margin: 0; padding: 0; box-sizing: border-box; }
  html, body { width: 900px; height: 1200px; overflow: hidden; }
  body {
    background: var(--backdrop);
    position: relative;
    font-family: "Marcellus SC", serif;
    color: var(--ink);
  }
  .card {
    position: absolute;
    left: 134px;
    width: 632px;
    height: 364px;
    background: linear-gradient(120deg, var(--card-dark) 0%, var(--card-light) 100%);
  }
  .card--front { top: 210px; }
  .card--back { top: 624px; }

  .brand-lockup {
    position: absolute;
    left: 0; right: 0;
    top: 138px;
    display: flex;
    justify-content: center;
    align-items: center;
    gap: 18px;
  }
  .brand-mark {
    width: 22px; height: 22px;
    background: var(--ink);
  }
  .brand-name {
    font-size: 46px;
    line-height: 1;
    letter-spacing: 1px;
    color: var(--ink);
  }
  .front-url {
    position: absolute;
    left: 0; right: 0;
    top: 318px;
    text-align: center;
    font-family: "Montserrat", sans-serif;
    font-weight: 600;
    font-size: 11.5px;
    letter-spacing: 4px;
    color: var(--ink);
  }

  .back-brand {
    position: absolute;
    left: 40px; top: 46px;
    font-size: 31px;
    line-height: 1;
    letter-spacing: 0.5px;
  }
  .person-name {
    position: absolute;
    left: 40px; top: 180px;
    font-size: 27px;
    line-height: 1;
    letter-spacing: 0.5px;
  }
  .person-role {
    position: absolute;
    left: 40px; top: 213px;
    font-size: 15.5px;
    line-height: 1;
    color: var(--ink-soft);
    letter-spacing: 0.5px;
  }
  .contact-list {
    position: absolute;
    left: 40px; top: 246px;
    list-style: none;
  }
  .contact-item {
    display: flex;
    align-items: center;
    gap: 5px;
    height: 27px;
    font-size: 13px;
    letter-spacing: 0.4px;
    color: var(--ink-soft);
  }
  .contact-item--phone { font-size: 16px; letter-spacing: 2px; }
  .contact-icon { width: 14px; height: 14px; fill: var(--ink-soft); flex: none; }
</style>
</head>
<body>
  <section class="card card--front" aria-label="Card front">
    <div class="brand-lockup">
      <span class="brand-mark" aria-hidden="true"></span>
      <span class="brand-name">OAK PARTNERS</span>
    </div>
    <p class="front-url">WWW.OAKPARTNERS.EXAMPLE</p>
  </section>

  <section class="card card--back" aria-label="Card back">
    <p class="back-brand">OAK PARTNERS</p>
    <p class="person-name">DORIAN PEMBERTON</p>
    <p class="person-role">ATTORNEY</p>
    <ul class="contact-list">
      <li class="contact-item contact-item--phone">
        <svg class="contact-icon" viewBox="0 0 24 24" aria-hidden="true"><path d="M6.6 10.8c1.4 2.8 3.8 5.1 6.6 6.6l2.2-2.2c.3-.3.7-.4 1-.2 1.1.4 2.3.6 3.6.6.6 0 1 .4 1 1V20c0 .6-.4 1-1 1C10.6 21 3 13.4 3 4c0-.6.4-1 1-1h3.5c.6 0 1 .4 1 1 0 1.3.2 2.5.6 3.6.1.3 0 .7-.2 1z"/></svg>
        <span>800-555-0147</span>
      </li>
      <li class="contact-item">
        <svg class="contact-icon" viewBox="0 0 24 24" aria-hidden="true"><path d="M2 5h20v14H2z M3 6l9 7 9-7" fill="none" stroke="#dfe4f3" stroke-width="2"/><path d="M2 5h20L12 13z"/></svg>
        <span>DORIAN@OAKPARTNERS.EXAMPLE</span>
      </li>
      <li class="contact-item">
        <svg class="contact-icon" viewBox="0 0 24 24" aria-hidden="true" fill="none" stroke="#dfe4f3" stroke-width="1.8"><circle cx="12" cy="12" r="9.5"/><ellipse cx="12" cy="12" rx="4" ry="9.5"/><path d="M2.5 12h19M4 7h16M4 17h16"/></svg>
        <span>WWW.OAKPARTNERS.EXAMPLE</span>
      </li>
    </ul>
  </section>
</body>
</html>
```